WordPress Design for both website and landing page for an expert

I need a clean and stylish design for my new website. I work as an expert (see attached file WHY HOW WHAT), my product is expert opinion (reports) for company evaluations You can use all of the attached pictures colored or black / white. The person is me, you can add other pictures, if you want. The design should be clean and stylish, so you could use white, black, gray, silver and / or one additional color. I have added an idea about my website, see attached file CONCEPT WEBSITE If you have any more information, please do not hesitate to contact us 'Hesitate to ask me ...

```html
<!DOCTYPE html>
<html lang="de">
<head>
<meta charset="utf-8">
<title>Lena Vorhoff – Sachverständige für Firmenbewertungen</title>
<link rel="stylesheet" href="https://fonts.googleapis.com/css2?family=Montserrat:wght@400;500;600&family=Open+Sans:ital,wght@0,400;0,600;1,400&display=swap">
<style>
:root{
  --blue:#3a5bc7;
  --blue-deep:#2f4fb4;
  --navy:#0d2a5c;
  --ink:#1d1d1f;
  --text:#555a63;
  --muted:#8a8f98;
  --line:#d5d9e2;
  --pale:#eef1f8;
  --chip:#dfe3ec;
  --white:#ffffff;
  --silver:#a9adb4;
}
*{margin:0;padding:0;box-sizing:border-box}
html,body{width:1200px;height:3020px;overflow:hidden;background:var(--white)}
body{position:relative;font-family:"Open Sans",Arial,sans-serif;color:var(--text)}
.abs{position:absolute}

/* Hero */
.hero{left:0;top:0;width:1200px;height:598px;
  background:linear-gradient(180deg,#0b2c6b 0%,#134a9a 35%,#2a66b4 52%,#20324f 70%,#3a3440 82%,#1b2232 100%)}
.hero-glow{left:0;top:400px;width:1200px;height:198px;
  background:radial-gradient(ellipse at 20% 40%,rgba(255,170,80,.35),transparent 55%),radial-gradient(ellipse at 80% 50%,rgba(255,120,80,.25),transparent 50%)}
.brand{left:110px;top:40px;width:310px;text-align:center}
.brand-mark{display:block;width:26px;height:26px;border-radius:50%;background:var(--white);margin:0 auto 22px}
.brand-name{font-family:"Montserrat",sans-serif;font-weight:400;font-size:27px;letter-spacing:5px;color:var(--white)}
.nav{top:68px;left:474px;display:flex;gap:32px;font-family:"Montserrat",sans-serif;font-size:15px;font-weight:500;color:var(--white);letter-spacing:.3px}
.nav .active{color:#6fa3ff}
.hero-title{top:240px;left:0;width:1200px;text-align:center;font-family:"Open Sans",sans-serif;font-weight:600;font-size:44px;color:var(--white)}
.hero-sub{top:312px;left:0;width:1200px;text-align:center;font-weight:600;font-size:23px;color:#e9eef8}
.slider-btn{top:568px;width:58px;height:58px;border-radius:50%;background:var(--white);box-shadow:0 2px 8px rgba(0,0,0,.18);display:flex;align-items:center;justify-content:center}

/* Why */
.section-title{left:0;width:1200px;text-align:center;font-family:"Montserrat",sans-serif;font-weight:500;font-size:46px;color:var(--ink);letter-spacing:.5px}
.circle{width:238px;height:238px;border-radius:50%;background:var(--white);box-shadow:0 3px 12px rgba(0,0,0,.18);display:flex;align-items:center;justify-content:center}
.circle.featured{background:var(--blue-deep);box-shadow:none}
.step-arrow{width:120px;height:120px;border-radius:50%;background:var(--chip);display:flex;align-items:center;justify-content:center}
.feature{top:1082px;width:300px;text-align:center}
.feature h3{font-family:"Montserrat",sans-serif;font-weight:500;font-size:25px;color:var(--ink);margin-bottom:22px}
.feature p{font-size:14px;line-height:27px;color:var(--text)}

/* FAQ */
.faq-band{left:0;top:1360px;width:1200px;height:836px;background:var(--pale)}
.faq-item{left:112px;width:976px;height:58px;background:var(--white);border:1px solid var(--line);display:flex;align-items:center}
.faq-item span{flex:1;padding-left:26px;font-size:15px;color:var(--ink)}
.faq-item i{width:60px;height:100%;border-left:1px solid var(--line);display:flex;align-items:center;justify-content:center}
.faq-lead{left:200px;top:1944px;width:800px;text-align:center;font-size:16.5px;line-height:31px;color:var(--text)}
.faq-note{left:220px;top:2040px;width:760px;text-align:center;font-style:italic;font-size:13px;line-height:26px;color:var(--text)}

/* Promise */
.promise{left:0;top:2196px;width:1200px;height:366px;background:linear-gradient(120deg,#4a6fcf 0%,#3c5fc3 50%,#4a6ed0 100%)}
.promise-title{top:2262px;font-family:"Montserrat",sans-serif;font-weight:500;font-size:44px;color:var(--white);left:0;width:1200px;text-align:center}
.promise-text{top:2334px;left:260px;width:680px;text-align:center;font-weight:600;font-size:18.5px;line-height:30px;color:var(--white)}
.promise-btn{top:2426px;left:492px;width:216px;height:62px;border:2px solid var(--white);border-radius:31px;display:flex;align-items:center;justify-content:center;font-family:"Montserrat",sans-serif;font-weight:600;font-size:16px;color:var(--white);letter-spacing:.5px}

/* Footer */
.foot-brand{left:110px;top:2760px;width:280px;text-align:center}
.foot-brand .brand-mark{background:var(--silver);margin-bottom:20px}
.foot-brand .brand-name{color:#8c9097;font-size:25px}
.foot-col h4{font-family:"Montserrat",sans-serif;font-weight:500;font-size:19px;color:var(--ink);margin-bottom:20px}
.foot-links{list-style:none;font-size:12.5px;line-height:25px;color:var(--text)}
.foot-small{font-size:12.5px;line-height:21px;color:var(--text)}
.email-field{margin-top:26px;width:252px;border-bottom:1px solid var(--line);padding-bottom:10px;font-size:12.5px;color:var(--ink)}
.subscribe{margin-top:16px;width:120px;height:44px;border:2px solid var(--blue);border-radius:22px;display:flex;align-items:center;justify-content:center;font-family:"Montserrat",sans-serif;font-weight:600;font-size:14px;color:var(--blue-deep)}
.contact-row{display:flex;align-items:center;gap:18px;font-size:12.5px;color:var(--text);height:51px}
.foot-rule{left:110px;top:2920px;width:980px;height:1px;background:var(--line)}
.copyright{left:110px;top:2960px;font-size:12px;color:var(--text)}
.social{top:2952px;width:34px;height:34px;border-radius:50%;border:1.5px solid var(--blue);display:flex;align-items:center;justify-content:center}
.social b{width:10px;height:10px;border-radius:50%;background:var(--blue)}
</style>
</head>
<body>

<header>
  <div class="abs hero" role="img" aria-label="Evening city skyline with a river, bridge and TV tower under a deep blue sky"></div>
  <div class="abs hero-glow" aria-hidden="true"></div>
  <div class="abs brand"><span class="brand-mark"></span><span class="brand-name">LENA VORHOFF</span></div>
  <nav class="abs nav">
    <span class="active">HOME</span><span>WHAT I DO</span><span>WHY I DO IT &amp; HOW I DO IT</span><span>ABOUT ME</span><span>CONTACT</span>
  </nav>
  <h1 class="abs hero-title">Sachverständiger für Firmenbewertungen</h1>
  <p class="abs hero-sub">Sie benötigen ein Gutachten zur Ermittlung des Wertes Ihres Unternehmens</p>
  <div class="abs slider-btn" style="left:540px"><svg width="16" height="16" viewBox="0 0 16 16"><path d="M10 2 4 8l6 6" fill="none" stroke="#555" stroke-width="1.8"/></svg></div>
  <div class="abs slider-btn" style="left:600px"><svg width="16" height="16" viewBox="0 0 16 16"><path d="M6 2l6 6-6 6" fill="none" stroke="#555" stroke-width="1.8"/></svg></div>
</header>

<section>
  <h2 class="abs section-title" style="top:698px">WHY CHOOSE US</h2>

  <div class="abs circle" style="left:140px;top:806px">
    <svg width="90" height="90" viewBox="0 0 90 90" fill="none" stroke="#6b6f77" stroke-width="2" stroke-linejoin="round">
      <path d="M82 8 8 44l26 10 8 28 14-20 26-54z"/><path d="M34 54 82 8 42 82"/>
    </svg>
  </div>
  <div class="abs step-arrow" style="left:368px;top:866px">
    <svg width="44" height="44" viewBox="0 0 44 44" fill="none" stroke="var(--blue)" stroke-width="4"><path d="M8 8l14 14-14 14M22 8l14 14-14 14"/></svg>
  </div>
  <div class="abs circle featured" style="left:481px;top:806px">
    <svg width="100" height="100" viewBox="0 0 100 100" fill="none" stroke="#fff" stroke-width="2">
      <path d="M50 8l8 12 14-6 2 15 15 3-6 14 12 9-12 9 6 14-15 3-2 15-14-6-8 12-8-12-14 6-2-15-15-3 6-14-12-9 12-9-6-14 15-3 2-15 14 6z"/>
    </svg>
  </div>
  <div class="abs step-arrow" style="left:710px;top:866px">
    <svg width="44" height="44" viewBox="0 0 44 44" fill="none" stroke="var(--blue)" stroke-width="4"><path d="M8 8l14 14-14 14M22 8l14 14-14 14"/></svg>
  </div>
  <div class="abs circle" style="left:821px;top:806px">
    <svg width="70" height="96" viewBox="0 0 70 96" fill="none" stroke="#6b6f77" stroke-width="2">
      <path d="M35 4C18 4 6 17 6 33c0 12 8 19 12 27 2 4 2 8 2 12h30c0-4 0-8 2-12 4-8 12-15 12-27C64 17 52 4 35 4z"/>
      <path d="M22 80h26M24 88h22M28 56l7-12 7 12"/>
    </svg>
  </div>

  <div class="abs feature" style="left:110px"><h3>Schnell</h3><p>Sie bekommen Ihr Gutachten zeitnah (innerhalb von max. 21 Tagen nach Zugang aller benötigten Unterlagen)</p></div>
  <div class="abs feature" style="left:450px"><h3>Zertifiziert</h3><p>Sie erhalten ein qualifiziertes und belastbares Gutachten von einem zertifizierten Sachverständigen (höchste Akzeptanz bei allen Parteien)</p></div>
  <div class="abs feature" style="left:790px"><h3>Verständlich</h3><p>Ihr Gutachten wird für Sie logisch und nachvollziehbar sein und kein "Fachchinesisch" enthalten</p></div>
</section>

<section>
  <div class="abs faq-band"></div>
  <h2 class="abs section-title" style="top:1442px">FREQUENTLY ASKED QUESTIONS</h2>
  <div class="abs faq-item" style="top:1541px"><span>What are the buying motives of the customers?</span><i><svg width="16" height="10" viewBox="0 0 16 10"><path d="M1 1l7 7 7-7" fill="none" stroke="#666" stroke-width="1.6"/></svg></i></div>
  <div class="abs faq-item" style="top:1618px"><span>Was sind die Kaufmotive der Kunden?</span><i><svg width="16" height="10" viewBox="0 0 16 10"><path d="M1 1l7 7 7-7" fill="none" stroke="#666" stroke-width="1.6"/></svg></i></div>
  <div class="abs faq-item" style="top:1696px"><span>Sie wollen Anteile Ihres Unternehmens oder ihr gesamtes Unternehmen verkaufen?</span><i><svg width="16" height="10" viewBox="0 0 16 10"><path d="M1 1l7 7 7-7" fill="none" stroke="#666" stroke-width="1.6"/></svg></i></div>
  <div class="abs faq-item" style="top:1773px"><span>Sie wollen Ihr Unternehmen auf Ihre Erben übertragen und benötigen eine Bewertung für das Finanzamt?</span><i><svg width="16" height="10" viewBox="0 0 16 10"><path d="M1 1l7 7 7-7" fill="none" stroke="#666" stroke-width="1.6"/></svg></i></div>
  <div class="abs faq-item" style="top:1850px"><span>Sie müssen im Rahmen einer Trennung/Scheidung jemanden ausbezahlen und benötigen eine Bemessungsgrundlage?</span><i><svg width="16" height="10" viewBox="0 0 16 10"><path d="M1 1l7 7 7-7" fill="none" stroke="#666" stroke-width="1.6"/></svg></i></div>
  <p class="abs faq-lead">Lassen Sie Ihr Unternehmen von einem qualifizierten Sachverständigen bewerten und gehen somit vielen (unnötigen) Streitereien aus dem Weg.</p>
  <p class="abs faq-note">Merke: Die Kosten für ein Gutachten sind immer überproportional günstiger als die Kosten für Rechtsstreitigkeiten. Und das losgelöst von der psychischen Belastung einer solchen Auseinandersetzung ...</p>
</section>

<section>
  <div class="abs promise" role="img" aria-label="Blue-tinted photo of a hand writing on documents with a pen"></div>
  <h2 class="abs promise-title">MY QUALITY PROMISE</h2>
  <p class="abs promise-text">Should the advised date for the preparation of the report be exceeded, you will receive the report free of chare</p>
  <div class="abs promise-btn">I WAIVE MY FEE</div>
</section>

<footer>
  <div class="abs brand foot-brand"><span class="brand-mark"></span><span class="brand-name">LENA VORHOFF</span></div>

  <div class="abs foot-col" style="left:440px;top:2674px">
    <h4>Information</h4>
    <ul class="foot-links"><li>Help</li><li>FAQ</li><li>Support</li><li>Sitemap</li><li>Terms Of Use</li><li>Privacy Statement</li></ul>
  </div>

  <div class="abs foot-col" style="left:610px;top:2674px">
    <h4>Newsletter Subscription</h4>
    <p class="foot-small">Register your Email Address to get<br>Information about us</p>
    <div class="email-field">Email Address</div>
    <div class="subscribe">SUBSCRIBE</div>
  </div>

  <div class="abs foot-col" style="left:904px;top:2674px">
    <h4>Contact Us</h4>
    <div class="contact-row" style="margin-top:-8px">
      <svg width="12" height="16" viewBox="0 0 12 16"><path d="M6 0a6 6 0 0 0-6 6c0 4 6 10 6 10s6-6 6-10a6 6 0 0 0-6-6zm0 8.5A2.5 2.5 0 1 1 6 3.5a2.5 2.5 0 0 1 0 5z" fill="var(--navy)"/></svg>
      <span>Talstraße 12, Musterstadt</span></div>
    <div class="contact-row">
      <svg width="13" height="13" viewBox="0 0 24 24"><path d="M6.6 10.8a15 15 0 0 0 6.6 6.6l2.2-2.2c.3-.3.7-.4 1-.2 1.1.4 2.3.6 3.6.6.6 0 1 .4 1 1V20c0 .6-.4 1-1 1A17 17 0 0 1 3 4c0-.6.4-1 1-1h3.5c.6 0 1 .4 1 1 0 1.3.2 2.5.6 3.6.1.3 0 .7-.2 1z" fill="var(--navy)"/></svg>
      <span>+49 000 123 4567</span></div>
    <div class="contact-row">
      <svg width="15" height="11" viewBox="0 0 15 11"><rect width="15" height="11" rx="1" fill="var(--navy)"/><path d="M1 1l6.5 5L14 1" fill="none" stroke="#fff" stroke-width="1.2"/></svg>
      <span>info@lenavorhoff.example</span></div>
  </div>

  <div class="abs foot-rule"></div>
  <p class="abs copyright">Copyrights © 2018, Lena Vorhoff. All rights reserved.</p>
  <div class="abs social" style="left:967px"><b></b></div>
  <div class="abs social" style="left:1010px"><b></b></div>
  <div class="abs social" style="left:1053px"><b></b></div>
</footer>

</body>
</html>
```